Poetry Book Cover Design Project

Looking for a minimalistic book cover design for a collection of poems. The book title is "Before The Lanterns Drift Away Slowly". There are three parts to the book. First covers poetry in the theme of Rage. Second love and desire. The third is strange poems. Essentially the sections are "Rage", "Desire" and the "Strange". The reason for the title "Before The Lanterns Drift Away Slowly" is as if someone is writing these till life changes towards the intended outcome as felt in each poem. I want to have the author's name "Ruvinath Kolongaswe" at the bottom. Ilustration attached.
- Minimalistic

```html
<!DOCTYPE html>
<html lang="en">
<head>
<meta charset="utf-8">
<title>Before The Lanterns Drift Away Slowly — Ruvinath Kolongaswe</title>
<link rel="stylesheet" href="https://fonts.googleapis.com/css2?family=Sorts+Mill+Goudy&display=swap">
<style>
  :root {
    --sky-top: #38aedb;
    --sky-mid: #6fcde6;
    --sky-haze: #e4f8fb;
    --sky-low: #a6e2ec;
    --sky-bottom: #8fd9e6;
    --stone-light: #b9bcbd;
    --stone-dark: #8c9193;
    --ink: #1f1f1c;
  }
  html, body {
    margin: 0;
    padding: 0;
    width: 800px;
    height: 1200px;
    overflow: hidden;
  }
  .cover {
    position: relative;
    width: 800px;
    height: 1200px;
    overflow: hidden;
    background: linear-gradient(180deg,
      var(--sky-top) 0%,
      var(--sky-mid) 35%,
      var(--sky-haze) 62%,
      var(--sky-low) 82%,
      var(--sky-bottom) 100%);
    font-family: "Sorts Mill Goudy", "Goudy Old Style", Georgia, serif;
    color: var(--ink);
  }
  .cover-illustration {
    position: absolute;
    left: 0;
    top: 168px;
    width: 350px;
    height: 620px;
    display: block;
  }
  .title {
    position: absolute;
    right: 44px;
    top: 150px;
    margin: 0;
    font-weight: 400;
    font-size: 100px;
    line-height: 142px;
    letter-spacing: -2px;
    text-align: right;
  }
  .title span {
    display: block;
  }
  .author {
    position: absolute;
    left: 0;
    right: 0;
    top: 1072px;
    margin: 0;
    text-align: center;
    font-size: 42px;
    font-weight: 400;
    letter-spacing: 5px;
  }
</style>
</head>
<body>
  <main class="cover">
    <svg class="cover-illustration" viewBox="0 0 350 620" role="img"
         aria-label="Illustration: a man stands at the broken end of a grey arched concrete bridge, looking down into the open sky">
      <defs>
        <linearGradient id="stoneTone" x1="0" y1="0" x2="1" y2="1">
          <stop offset="0%" stop-color="var(--stone-light)"/>
          <stop offset="100%" stop-color="var(--stone-dark)"/>
        </linearGradient>
      </defs>
      <rect x="0" y="0" width="350" height="620" rx="6" fill="url(#stoneTone)" opacity="0.55"/>
    </svg>

    <h1 class="title">
      <span>Before</span>
      <span>The</span>
      <span>Lanterns</span>
      <span>Drift</span>
      <span>Away</span>
      <span>Slowly</span>
    </h1>

    <p class="author">Ruvinath Kolongaswe</p>
  </main>
</body>
</html>
```